Panty packaging

what we are looking for is 1 of a kind packaging for women's panties. It should have the same theme for all styles but a different outline or a color code setting the difference between styles. Most company's are packaging in a poly bag or hanger, what we are looking for is a box packaging. also customer should be able to see whats in the box without having to open the box. If there are different colors, the window should show that. We want to be able to customize the design for different styles and for 1 color package or multi color package. It should be sleek and sophisticated. Box does not have to be square, it can have curved edges or be totally round, the most important thins is that it should be stack-able. Sometimes the box will hold a pack of 3 and sometimes a single item, so box height may vary. We need a graphic on the box to indicate the style, for example: hipster, brief, hi cut, or lo cut. box needs a space to put a small size chart. Out logo can be color changed to match theme and background colors, just stick with the 3 colors, black, white, and magneta.
Female market all ages. upscale market
It Company

```html
<!DOCTYPE html>
<html lang="en">
<head>
<meta charset="utf-8">
<title>Velmora — Panty Box</title>
<link rel="stylesheet" href="https://fonts.googleapis.com/css2?family=Questrial&family=Fondamento&display=swap">
<style>
  :root {
    --backdrop-top: #8a8776;
    --backdrop-bottom: #f4efe3;
    --box-white: #f6f6f6;
    --box-side: #ececec;
    --box-edge: #d6d6d6;
    --ink: #1a1a1a;
    --magenta: #e6007e;
    --blue: #1565e6;
    --orange: #ef8a12;
    --lime: #8ee21c;
    --icon-grey: #9e9a8c;
    --product-tan: #d9bfa0;
    --product-shade: #bf9f7d;
    --ring: #9a9a9a;
  }
  * { margin: 0; padding: 0; box-sizing: border-box; }
  html, body { width: 1200px; height: 800px; overflow: hidden; }
  body {
    background: linear-gradient(180deg, var(--backdrop-top) 0%, #c9c3b0 45%, var(--backdrop-bottom) 100%);
    position: relative;
    font-family: "Questrial", sans-serif;
    color: var(--ink);
  }

  /* ---------- Box ---------- */
  .box {
    position: absolute;
    left: 90px; top: 110px;
    width: 640px;
    box-shadow: 0 18px 40px rgba(60, 55, 40, .25);
  }
  .box-top {
    height: 330px;
    background: var(--box-white);
    border: 1px solid var(--box-edge);
    display: flex;
  }
  .sleeve {
    width: 330px;
    display: flex; align-items: center; justify-content: center;
    border-right: 1px solid var(--box-edge);
  }
  .brand-name {
    font-family: "Questrial", sans-serif;
    font-size: 58px; letter-spacing: 2px;
    color: var(--ink);
  }
  .window {
    width: 90px;
    margin: 22px 0;
    border: 6px solid #fff;
    outline: 1px solid var(--box-edge);
    background: linear-gradient(90deg, var(--product-shade), var(--product-tan) 40%, var(--product-tan));
  }
  .tray {
    flex: 1;
    position: relative;
    border-left: 1px solid var(--box-edge);
  }
  .style-dot {
    position: absolute; left: 92px; top: 60px;
    width: 34px; height: 34px; border-radius: 50%;
    background: var(--magenta);
  }
  .size-strip {
    position: absolute; left: 22px; right: 22px; bottom: 36px;
    display: flex; align-items: flex-end; justify-content: space-between;
    font-family: "Fondamento", serif; font-size: 14px;
  }
  .size-option { display: flex; flex-direction: column; align-items: center; gap: 3px; }
  .ring { width: 10px; height: 10px; border-radius: 50%; border: 1px solid var(--ring); }
  .size-strip .ring.is-selected { background: var(--magenta); border-color: var(--magenta); }

  .box-side {
    height: 76px;
    background: var(--box-side);
    border: 1px solid var(--box-edge);
    border-top: none;
    display: flex; align-items: center;
    padding: 0 28px;
  }
  .side-brand {
    font-family: "Questrial", sans-serif;
    font-size: 18px; letter-spacing: 1px;
    margin-right: auto;
  }
  .side-legend {
    list-style: none;
    display: grid;
    grid-template-columns: repeat(2, 118px);
    row-gap: 6px;
    font-family: "Fondamento", serif; font-size: 13px;
  }
  .side-legend li { display: flex; align-items: center; }
  .side-legend .legend-dot { width: 9px; height: 9px; margin-right: 8px; }
  .side-legend .legend-icon { width: 22px; height: 15px; margin-right: 8px; }

  /* ---------- Shared legend parts ---------- */
  .legend-dot { border-radius: 50%; flex: none; }
  .dot-brief { background: var(--magenta); }
  .dot-hipster { background: var(--blue); }
  .dot-hicut { background: var(--orange); }
  .dot-locut { background: var(--lime); }
  .legend-icon { flex: none; fill: var(--icon-grey); }

  /* ---------- Swatch sheet ---------- */
  .style-legend {
    position: absolute; left: 765px; top: 562px;
    list-style: none;
    font-family: "Fondamento", serif; font-size: 16px;
  }
  .style-legend li { display: flex; align-items: center; height: 40px; }
  .style-legend .legend-dot { width: 14px; height: 14px; margin-right: 16px; }
  .style-legend .legend-icon { width: 32px; height: 22px; margin-right: 16px; }

  .sizing-chart {
    position: absolute; left: 940px; top: 588px;
    width: 140px;
    font-family: "Fondamento", serif;
  }
  .sizing-chart h2 { font-weight: 400; font-size: 16px; text-align: center; margin-bottom: 22px; }
  .sizing-row { display: flex; justify-content: space-between; }
  .sizing-row .size-option { font-size: 17px; gap: 8px; }
  .sizing-row .ring { width: 15px; height: 15px; }
  .sizing-row .ring.is-selected { background: var(--lime); border-color: var(--lime); }
</style>
</head>
<body>
  <svg width="0" height="0" style="position:absolute">
    <defs>
      <path id="shape-brief" d="M2 2 H30 V10 Q22 14 18 20 H14 Q10 14 2 10 Z"/>
      <path id="shape-hipster" d="M2 4 H30 V14 Q22 14 18 20 H14 Q10 14 2 14 Z"/>
      <path id="shape-hicut" d="M2 4 Q16 8 30 4 L18 18 H14 Z"/>
      <path id="shape-locut" d="M2 6 H30 L20 18 H12 Z"/>
    </defs>
  </svg>

  <section class="box">
    <div class="box-top">
      <div class="sleeve">
        <span class="brand-name">VELMORA</span>
      </div>
      <div class="window" role="img" aria-label="Window showing the folded nude-tone panties inside the box"></div>
      <div class="tray">
        <span class="style-dot"></span>
        <div class="size-strip">
          <span class="size-label">Size</span>
          <span class="size-option"><span class="ring"></span>5</span>
          <span class="size-option"><span class="ring is-selected"></span>6</span>
          <span class="size-option"><span class="ring"></span>7</span>
          <span class="size-option"><span class="ring"></span>8</span>
          <span class="size-option"><span class="ring"></span>9</span>
        </div>
      </div>
    </div>
    <div class="box-side">
      <span class="side-brand">VELMORA</span>
      <ul class="side-legend">
        <li><span class="legend-dot dot-brief"></span><svg class="legend-icon" viewBox="0 0 32 22"><use href="#shape-brief"/></svg>Brief</li>
        <li><span class="legend-dot dot-hicut"></span><svg class="legend-icon" viewBox="0 0 32 22"><use href="#shape-hicut"/></svg>Hi Cut</li>
        <li><span class="legend-dot dot-hipster"></span><svg class="legend-icon" viewBox="0 0 32 22"><use href="#shape-hipster"/></svg>Hipster</li>
        <li><span class="legend-dot dot-locut"></span><svg class="legend-icon" viewBox="0 0 32 22"><use href="#shape-locut"/></svg>Lo Cut</li>
      </ul>
    </div>
  </section>

  <ul class="style-legend">
    <li><span class="legend-dot dot-brief"></span><svg class="legend-icon" viewBox="0 0 32 22"><use href="#shape-brief"/></svg>Brief</li>
    <li><span class="legend-dot dot-hipster"></span><svg class="legend-icon" viewBox="0 0 32 22"><use href="#shape-hipster"/></svg>Hipster</li>
    <li><span class="legend-dot dot-hicut"></span><svg class="legend-icon" viewBox="0 0 32 22"><use href="#shape-hicut"/></svg>Hi Cut</li>
    <li><span class="legend-dot dot-locut"></span><svg class="legend-icon" viewBox="0 0 32 22"><use href="#shape-locut"/></svg>Lo Cut</li>
  </ul>

  <section class="sizing-chart">
    <h2>Sizing</h2>
    <div class="sizing-row">
      <span class="size-option"><span class="ring"></span>5</span>
      <span class="size-option"><span class="ring is-selected"></span>6</span>
      <span class="size-option"><span class="ring"></span>7</span>
      <span class="size-option"><span class="ring"></span>8</span>
      <span class="size-option"><span class="ring"></span>9</span>
    </div>
  </section>
</body>
</html>
```